Digital One Pager for Consulting Practice

I would like the essence of the content in my ppt consolidated into a one-pager. The one-pager will mainly be sent via email as a pdf and intended to excite and invite new clients and establish the credibility of my boutique high-end consulting firm. Infographics and symbols would be a plus. The target client should view the firm as providing premeir service. The client is getting a thought partner.

Target Market(s)

Large Medical Device Manufacturer Executives, Early-Stage Medical Device Manufacturer Executives, Partners at VC Firms

Industry/Entity Type

Medical Equipment

Colors
0355a3
f37122

Requirements
Must have
• Please match the color scheme in ppt. Please use the existing logo. I am very open to better graphics on the process. My photo does not need to be on the digital flyer. Hyper link to the website and email is needed.
Nice to have
• Infographics

```html
<!DOCTYPE html>
<html lang="en">
<head>
<meta charset="utf-8">
<title>Halden Ventures – One Pager</title>
<link href="https://fonts.googleapis.com/css2?family=Montserrat:wght@400;500;600;700;800&display=swap" rel="stylesheet">
<style>
  :root{
    --navy:#13213b;
    --orange:#e9553a;
    --grey:#857d78;
    --ink:#1b2233;
    --paper:#ffffff;
    --stage:#e7e4e0;
    --badge:#d7dae0;
  }
  *{box-sizing:border-box;margin:0;padding:0}
  html,body{width:1200px;height:1200px;overflow:hidden;background:var(--stage);font-family:'Montserrat',sans-serif;color:var(--ink)}
  .sheet{position:absolute;left:170px;top:40px;width:860px;height:1120px;background:var(--paper);overflow:hidden;box-shadow:0 6px 24px rgba(0,0,0,.18)}
  .sheet-shapes{position:absolute;inset:0}
  .abs{position:absolute}
  .brand{left:44px;top:58px;display:flex;align-items:center;gap:14px}
  .brand-mark{width:46px;height:46px;border:5px solid var(--navy);border-radius:50%}
  .brand-name{font-weight:800;font-size:46px;color:var(--navy);letter-spacing:3px;line-height:1}
  .brand-sub{font-weight:800;font-size:46px;color:var(--navy);letter-spacing:3px;line-height:1}
  .tagline{left:400px;top:48px;width:440px;text-align:center;font-weight:800;font-size:29px;line-height:1.12;color:var(--ink)}
  .tagline .hot{color:var(--orange)}
  .portrait{left:110px;top:205px;width:210px;height:210px;border-radius:50%;background:radial-gradient(circle at 50% 40%,#9a8f8a,#4a4c55);border:6px solid #d9d9d9}
  .provide{left:400px;top:178px;width:440px}
  h2.provide-title{font-size:22px;font-weight:800;margin-bottom:6px}
  .sub{color:var(--orange);font-weight:600;font-size:13px;margin:6px 0 3px}
  ul.ticks{list-style:none}
  ul.ticks li{position:relative;padding-left:20px;font-size:12.5px;line-height:1.3;margin-bottom:4px}
  ul.ticks li::before{content:"";position:absolute;left:2px;top:3px;width:10px;height:10px;border:1.5px solid currentColor;border-radius:50%}
  ul.ticks li::after{content:"";position:absolute;left:5px;top:5px;width:3px;height:5px;border:solid currentColor;border-width:0 1.5px 1.5px 0;transform:rotate(40deg)}
  .experience{left:40px;top:418px;width:460px;color:#fff}
  .experience h2{color:var(--orange);font-size:25px;font-weight:700;margin-bottom:8px}
  .experience ul.ticks li{font-size:13.5px;margin-bottom:6px}
  .experience ul.ticks li::before,.services ul.ticks li::before{border-color:var(--orange)}
  .experience ul.ticks li::after,.services ul.ticks li::after{border-color:var(--orange)}
  .services{left:40px;top:690px;width:470px;color:#fff}
  .services h2{font-size:27px;font-weight:700;margin-bottom:6px}
  .svc-cols{display:flex;gap:26px}
  .svc-col{flex:1}
  .svc-col h3{color:var(--orange);font-size:15px;font-weight:600;margin:10px 0 5px}
  .svc-col ul.ticks li{font-size:13px}
  .diff{left:540px;top:410px;width:300px}
  h2.sec{font-size:18px;font-weight:800}
  .donut{left:570px;top:445px;width:250px;height:250px}
  .process{left:530px;top:720px;width:320px}
  .steps{position:relative;height:100px;margin-top:8px}
  .step{position:absolute;width:80px;height:52px;display:flex;align-items:center;justify-content:center;text-align:center;color:#fff;font-size:11.5px;font-weight:500;line-height:1.15}
  .step.navy{background:var(--navy)}
  .step.orange{background:var(--orange)}
  .partners{left:540px;top:850px;width:300px}
  .badges{display:grid;grid-template-columns:repeat(3,1fr);gap:12px;margin-top:12px}
  .badge{height:34px;background:var(--badge);border-radius:4px}
  .badge.dark{background:#4b5166}
  .badge.blue{background:#2d6fb8}
  .contact{left:540px;top:1030px;color:#fff;font-size:15px;font-weight:500;line-height:1.9}
  .contact a{color:#fff;text-decoration:none}
  .contact .row{display:flex;align-items:center;gap:8px}
  .web{left:30px;top:1078px;color:#fff;font-size:17px;letter-spacing:4px;font-weight:500;text-decoration:none}
</style>
</head>
<body>
<main class="sheet">
  <svg class="sheet-shapes" width="860" height="1120" viewBox="0 0 860 1120" aria-hidden="true">
    <rect x="0" y="355" width="16" height="720" fill="var(--orange)"/>
    <path d="M14,370 H430 Q520,370 520,460 V950 Q520,1005 590,1005 H860 V1120 H14 Z" fill="var(--navy)"/>
    <path d="M0,1065 H370 C430,1065 450,1020 520,1020 V1120 H0 Z" fill="var(--orange)"/>
  </svg>

  <div class="abs brand">
    <div class="brand-mark"></div>
    <div><div class="brand-name">HALDEN</div><div class="brand-sub" style="font-size:20px;letter-spacing:8px">VENTURES</div></div>
  </div>

  <h1 class="abs tagline">Extensive Experience<br><span class="hot">Efficient Process</span><br>Valued Network</h1>

  <div class="abs portrait" role="img" aria-label="Portrait photo of the firm's founder"></div>

  <section class="abs provide">
    <h2 class="provide-title">Experience to Provide...</h2>
    <p class="sub">Executive Application Review</p>
    <ul class="ticks">
      <li>Examples include: Presubmission, IDE, 510(k), 513(g), PMA, Refuse to Accept, Hold letter</li>
      <li>Troubleshooting</li>
    </ul>
    <p class="sub">Strategic Advice &amp; Diligence to Investors</p>
    <ul class="ticks">
      <li>Validate &amp; Verify Founder Milestones</li>
      <li>Diligence portfolio company Regulatory and Quality systems</li>
    </ul>
  </section>

  <section class="abs experience">
    <h2>Experience</h2>
    <ul class="ticks">
      <li>Over a decade @FDA (Former Deputy Division Director)</li>
      <li>Expertise: Cardiovascular, Ophthalmology, General Hospital, Infection Control, Dental, Anesthesia, Respiratory</li>
      <li>Vice President Regulatory Affairs / Quality Assurance @Corvane (Fortune 150 Company)</li>
      <li style="margin-left:22px">Initiated reorganization of department</li>
      <li style="margin-left:22px">Led major compliance effort</li>
      <li style="margin-left:22px">Successful FDA inspection (no observations)</li>
    </ul>
  </section>

  <section class="abs services">
    <h2>Services</h2>
    <div class="svc-cols">
      <div class="svc-col">
        <h3>Regulatory Strategy</h3>
        <ul class="ticks"><li>RAQA Organizational Structure</li><li>Regulatory Pathway</li></ul>
        <h3>Interim Executive Leadership</h3>
        <ul class="ticks"><li>Compliance Remediation</li><li>Accelerated Product Registration</li></ul>
      </div>
      <div class="svc-col">
        <h3>FDA Communications</h3>
        <ul class="ticks"><li>Deficiency Response</li><li>Application Review</li></ul>
        <h3>Training</h3>
        <ul class="ticks"><li>FDA Communication</li><li>MDR Reporting</li></ul>
      </div>
    </div>
  </section>

  <h2 class="abs sec diff">Differentiators</h2>
  <svg class="abs donut" viewBox="0 0 250 250" role="img" aria-label="Leverage cycle: Network, Process, Experience">
    <path d="M27,105 A100,100 0 0 1 200,58 L160,98 A50,50 0 0 0 77,115 Z" fill="var(--navy)"/>
    <path d="M204,62 A100,100 0 0 1 145,223 L133,173 A50,50 0 0 0 164,102 Z" fill="var(--orange)"/>
    <path d="M140,224 A100,100 0 0 1 26,112 L76,120 A50,50 0 0 0 128,174 Z" fill="var(--grey)"/>
    <circle cx="125" cy="125" r="48" fill="#fff"/>
    <text x="125" y="131" text-anchor="middle" font-family="Montserrat,sans-serif" font-weight="700" font-size="15" fill="var(--ink)">LEVERAGE</text>
    <text x="105" y="60" text-anchor="middle" font-family="Montserrat,sans-serif" font-size="12" fill="#fff">Network</text>
    <text x="196" y="145" text-anchor="middle" font-family="Montserrat,sans-serif" font-size="12" fill="#fff">Process</text>
    <text x="80" y="195" text-anchor="middle" font-family="Montserrat,sans-serif" font-size="12" fill="#fff">Experience</text>
    <circle cx="165" cy="50" r="12" fill="none" stroke="#fff" stroke-width="2"/>
    <circle cx="52" cy="138" r="12" fill="none" stroke="#fff" stroke-width="2"/>
    <circle cx="190" cy="178" r="12" fill="none" stroke="#fff" stroke-width="2"/>
  </svg>

  <section class="abs process">
    <h2 class="sec">Efficient Process</h2>
    <div class="steps">
      <div class="step navy" style="left:0;top:48px">Exploratory Call</div>
      <div class="step orange" style="left:80px;top:32px">Regulatory Landscape</div>
      <div class="step navy" style="left:160px;top:16px">Problem Statement</div>
      <div class="step orange" style="left:240px;top:0">Review &amp; Align on Deliverables</div>
    </div>
  </section>

  <section class="abs partners">
    <h2 class="sec">Valued Partner Network</h2>
    <div class="badges">
      <div class="badge"></div><div class="badge"></div><div class="badge"></div>
      <div class="badge dark"></div><div class="badge"></div><div class="badge blue"></div>
    </div>
  </section>

  <div class="abs contact">
    <div class="row">
      <svg width="16" height="16" viewBox="0 0 24 24" aria-hidden="true"><path d="M6.6 10.8a15 15 0 0 0 6.6 6.6l2.2-2.2c.3-.3.7-.4 1-.2 1.1.4 2.3.6 3.6.6.6 0 1 .4 1 1V20c0 .6-.4 1-1 1A17 17 0 0 1 3 4c0-.6.4-1 1-1h3.5c.6 0 1 .4 1 1 0 1.3.2 2.5.6 3.6.1.3 0 .7-.2 1z" fill="#fff"/></svg>
      <span>555.014.2290</span>
    </div>
    <div class="row">
      <svg width="16" height="16" viewBox="0 0 24 24" aria-hidden="true"><rect x="2" y="5" width="20" height="14" rx="2" fill="none" stroke="#fff" stroke-width="2"/><path d="M3 6l9 7 9-7" fill="none" stroke="#fff" stroke-width="2"/></svg>
      <a href="mailto:info@haldenventures.com">info@haldenventures.com</a>
    </div>
  </div>

  <a class="abs web" href="https://www.haldenventures.com">www.haldenventures.com</a>
</main>
</body>
</html>
```